Medical Learning Web Design Project

The web site will be a site for medical students. It is aimed at providing a collaborative place for students to study, learn, question each other and challenge each other with learning. The site needs to have a section on the page that is for the content and this needs to be relatively clean and clinical. The surrounding elements will be informative (for the statistics, challenge etc). There will also be a slide-out screen that allows for the social/friend elements of the site.

The colour scheme needs to be clean and clinical where appropriate, but also engaging and exciting for the social/competitive elements.
Updates

Just for clarity: The site isn't expected to be 'coded' ... it is just the layered PSD files that I need.

Also, with regards to the navigation buttons ... they will never ALL be present at the same time so don't feel the need to design all on one page, but creativity around allowing few or many on a page will be an advantage ...

Thanks

Hi,

Please note that the image uploaded has been done as a wireframe by the developers. I am looking for a more creative and engaging way of presenting that content ...

Thanks

Hi all

Thank you all for the designs so far ...!

Please have a look at the new uploaded file, I am also looking not just for a 'templated home page' but also some different layouts that are represented in these wireframes. If the various layouts represented can be condensed down into 1 or 2 page templates with appropriate colour schemes to capture the type of content on the page (as already mentioned ... social .. competitive ... learning), then that will help me live the concepts better too! The friends tab for instance I have envisaged as a slider covering the screen and then sliding back when complete ... but let me see what creativity you can give to this ...!

Many thanks

Reason: Just allowing for final tweaks ...

Target Market(s)

Medical Students

Industry/Entity Type

Medical

Requirements
Must have
• - Not cluttered appearance
- Dynamic navigation (ie. site will be developed to only show relevant navigation buttons on each page ...)
- Navigation buttons (need to be individual buttons) will be: 'Home', 'Take the tour', 'What your peers say', 'Subscriptions', 'Free Signup', 'Contact us', 'Moderation', 'Statistics', 'Competition', 'Answer Questions', 'Post Questions', 'My profile', 'Friends'
- Please also ensure it is engaging for social elements and competitive elements (perhaps slightly different design for pages focussed on each element)
- Please also ensure that there is a masculine design and feminine design that has continuity for the site but depending on gender the design can be tailored to be more appealing (that means perhaps male social design, male competitive design, female social design, female competitive design ... without loosing continuity through the site).
- Photoshop PSD format
- Pixel perfect at least 1000 pixels wide (but the design needs to allow for various monitor sizes (only desktop or laptops ... not tablets or smart phones)

```html
<!DOCTYPE html>
<html lang="en">
<head>
<meta charset="utf-8">
<title>Clinova – The Medical Peer Review</title>
<link href="https://fonts.googleapis.com/css2?family=Play:wght@400;700&family=Arimo:wght@400;700&family=Delius&display=swap" rel="stylesheet">
<style>
:root{
  --teal-dark:#22696a;
  --teal-footer:#2d6a6b;
  --teal-board:#3b7f82;
  --sky:#a9dbe5;
  --sky-light:#c5e8ee;
  --tan:#e7bb88;
  --tan-text:#8c5b2e;
  --heading:#2b5e62;
  --body:#8a8a8a;
  --link:#4aaed6;
  --line:#c9e0e4;
  --foot-text:#b8d6d6;
}
*{box-sizing:border-box;margin:0;padding:0}
html,body{width:1200px;height:1200px;overflow:hidden;background:#fff}
body{position:relative;font-family:Arimo,Arial,sans-serif;color:var(--body)}
.abs{position:absolute}
h2,h3,.play{font-family:Play,Arial,sans-serif;font-weight:400;color:var(--heading)}

.header{left:0;top:0;width:1200px;height:122px;background:linear-gradient(100deg,#93d2de 0%,#b7e3ea 45%,#9fd7e2 100%)}
.brand{left:200px;top:30px;font-size:38px;color:#fff;font-family:Arimo,Arial,sans-serif;letter-spacing:-1px}
.tagline{left:200px;top:72px;font-size:10px;color:#2b8b9b}
.likebar{left:200px;top:98px;width:166px;height:24px;background:#fff;font-size:8.5px;color:#333;display:flex;align-items:center;gap:6px;padding-left:5px}
.likebar .btn{border:1px solid #c5cbd8;background:#eef1f7;color:#3b5998;padding:1px 4px;font-size:8px}
.likebar .sq{width:9px;height:9px;background:#3b5998}
.quote{left:540px;top:32px;width:371px;text-align:right;font-size:10px;color:#fff;line-height:14px}
.stats{left:563px;top:64px;font-size:18px;color:#4d8c97;letter-spacing:.5px}
.toplinks{left:908px;top:2px;font-size:8.5px;color:#5a9aa6;display:flex;gap:8px;align-items:center}
.toplinks .login{background:#7fbfcc;color:#fff;padding:2px 5px;border-radius:2px}
.nav{left:564px;top:98px;height:25px;display:flex;gap:1px}
.nav a{display:block;height:25px;line-height:25px;text-align:center;font-size:9.5px;color:var(--tan-text);background:linear-gradient(#eecb9f,#e3b47f);text-decoration:none}
.nav a.active{background:var(--teal-dark);color:#fff}

.stage{left:0;top:122px;width:1200px;height:363px;background:linear-gradient(90deg,#e9bf95 0%,#f3d6b9 18%,#d4e4df 40%,#e6c9a7 62%,#cfe2e6 80%,#efcba6 100%)}
.floor{left:0;top:395px;width:1200px;height:90px;background:linear-gradient(#e2c5a6,#f1e0cc)}
.shadow{left:230px;top:440px;width:740px;height:30px;border-radius:50%;background:radial-gradient(ellipse at center,rgba(80,50,30,.35),rgba(80,50,30,0) 70%)}
.frame{left:200px;top:138px;width:800px;height:308px;background:#fff}
.board{left:206px;top:143px;width:790px;height:298px;background:radial-gradient(ellipse at 30% 40%,#4a8e90,var(--teal-board) 60%,#33716f)}
.board h1{position:absolute;left:24px;top:43px;font-family:Delius,cursive;font-weight:400;font-size:18.5px;color:#fff}
.board ul{position:absolute;left:26px;top:74px;list-style:none;font-family:Delius,cursive;font-size:11.5px;color:#f1f6f5;line-height:19.2px}
.board li:before{content:"• ";font-size:8px}
.photo{left:579px;top:158px;width:400px;height:266px;background:linear-gradient(120deg,#eef2f3,#d7e1e4 55%,#f4f6f7)}
.arrow{top:280px;width:18px;height:32px;background:#f3f3f3;border:1px solid #d5d5d5}

.notice{left:0;top:485px;width:1200px;height:29px;background:var(--sky)}
.notice-label{left:200px;top:485px;height:29px;width:103px;font-size:10px;color:#fff;line-height:29px;padding-left:10px}
.notice-text{left:329px;top:494px;font-size:8.5px;color:#4b8089}
.notice-text u{color:#4b8089}
.social{left:855px;top:489px;display:flex;gap:4px}
.social span{width:21px;height:21px;border-radius:3px;display:block}

.section-title{font-size:22px}
.copy{font-size:9.5px;line-height:14.4px;color:#8d8d8d}
.readmore{left:547px;top:677px;width:80px;height:22px;background:var(--teal-dark);color:#fff;font-size:9px;text-align:center;line-height:22px;border-radius:2px}
.video{left:657px;top:570px;width:343px;height:128px;background:#c8d8da;border:1px solid #bcd0d3}
.divider{left:200px;top:721px;width:800px;height:4px;border-top:1px dotted #cfe1e4;border-bottom:1px dotted #cfe1e4}
.col-title{font-size:16px;top:745px}
.testi{left:200px;top:776px;width:291px;height:176px;border:1px solid var(--line);padding:22px 13px;font-size:8px;line-height:12.8px;text-align:justify;color:#939393}
.testi p+p{margin-top:13px}
.author{left:300px;top:973px;width:191px;text-align:right;font-size:9px;line-height:9.5px;color:#a8a8a8}
.author b{font-size:10px;color:#8c8c8c;display:block;margin-bottom:3px}
.likebox{left:521px;top:776px;width:224px;height:227px;border:1px solid var(--line)}
.followbox{left:774px;top:776px;width:226px;height:227px;border:1px solid var(--line);overflow:hidden}
.tweet{position:absolute;left:8px;width:208px;height:64px;border-bottom:1px dotted #cfcfcf}
.tweet .dot{position:absolute;left:3px;top:9px;width:20px;height:20px;border-radius:50%;background:#7fc4e3}
.tweet p{position:absolute;left:34px;top:8px;width:175px;font-size:9.4px;line-height:12px;color:#8c8c8c}
.tweet .url{display:block;font-size:7.8px;color:var(--link)}
.tweet .ago{display:block;font-size:7.8px;color:#b0b0b0}

.footer{left:0;top:1028px;width:1200px;height:172px;background:var(--teal-footer)}
.footer h3{position:absolute;color:#fff;font-size:18px;top:14px}
.footer ul{position:absolute;list-style:none;top:46px;font-size:9.6px;line-height:16.8px;color:var(--foot-text)}
.footer li:before{content:"» "}
.contact{position:absolute;left:467px;top:46px;font-size:9.6px;line-height:14.5px;color:var(--foot-text)}
.contact .strong{color:#fff;font-family:Play,Arial,sans-serif;letter-spacing:.5px}
.news{position:absolute;left:621px;top:47px;width:379px;font-size:8px;line-height:10.5px;color:var(--foot-text)}
.email{position:absolute;left:621px;top:80px;width:288px;height:28px;background:#e7f3f3;border:1px solid #a8c9c9;font-size:9px;color:#a9c0c0;padding:8px 10px}
.join{position:absolute;left:913px;top:80px;width:87px;height:28px;background:linear-gradient(#4b8888,#245a5a);color:#e6f1f1;font-size:11px;text-align:center;line-height:28px;border-radius:2px}
.copyright{position:absolute;left:620px;top:122px;font-size:9.6px;color:var(--foot-text);line-height:24px}
</style>
</head>
<body>

<header>
  <div class="abs header"></div>
  <div class="abs brand">Clinova</div>
  <div class="abs tagline">The Medical Peer Review</div>
  <div class="abs likebar"><span class="btn">Like</span><span class="sq"></span><span>1,029,780 people like this.</span></div>
  <div class="abs toplinks"><span>Contact</span><span class="login">➦ Login</span></div>
  <div class="abs quote">“ Clinova keeps me ahead of the game, constantly testing my knowledge... ”<br>Sam. Doctor in training Northfield University</div>
  <div class="abs stats play">How will your stats compare?</div>
  <nav class="abs nav">
    <a class="active" style="width:50px">Home</a>
    <a style="width:84px">Take the Tour</a>
    <a style="width:116px">What your Peers Say</a>
    <a style="width:105px">Subscription Plans</a>
    <a style="width:76px">Free Signup</a>
  </nav>
</header>

<section class="hero">
  <div class="abs stage"></div>
  <div class="abs floor"></div>
  <div class="abs shadow"></div>
  <div class="abs frame"></div>
  <div class="abs board">
    <h1>Lorem Ipsum is simply dummy text</h1>
    <ul>
      <li>Suspendisse luctus orci ac nisl ultricies quis.</li>
      <li>Integer euismod enim in quam molestie varius.</li>
      <li>Sed pellentesque odio in eros aliquam gravida.</li>
      <li>Curabitur volutpat mi nec metus fermentum congue.</li>
      <li>Phasellus eget dolor ut turpis luctus laoreet.</li>
      <li>Cras eget dolor a odio tempus sollicitudin.</li>
      <li>Quisque eu mi nunc, eget porttitor augue.</li>
      <li>Fusce sollicitudin adipiscing tellus, sit amet.</li>
      <li>Fusce sit amet odio tellus, eu gravida nibh.</li>
    </ul>
  </div>
  <div class="abs photo" role="img" aria-label="Photo of a medical student working with test tubes in a laboratory"></div>
  <div class="abs arrow" style="left:206px"><svg width="16" height="30"><path d="M6 11l4 4-4 4" fill="none" stroke="#888" stroke-width="1.5"/></svg></div>
  <div class="abs arrow" style="left:976px"><svg width="16" height="30"><path d="M10 11l-4 4 4 4" fill="none" stroke="#888" stroke-width="1.5"/></svg></div>
</section>

<section>
  <div class="abs notice"></div>
  <svg class="abs" style="left:200px;top:485px" width="104" height="29"><path d="M0 0H96L104 14.5 96 29H0z" fill="#2a6d6f"/></svg>
  <div class="abs notice-label">NOTIFICATIONS</div>
  <div class="abs notice-text">Clinova is now on our social page. Follow us here <u>social.example/clinova</u></div>
  <div class="abs social">
    <span style="background:#5aa33c"></span><span style="background:#d33b2f"></span><span style="background:#e23a3a"></span><span style="background:#2d77b4"></span><span style="background:#45b4e0"></span><span style="background:#3c5c9c"></span>
  </div>
</section>

<main>
  <h2 class="abs section-title" style="left:200px;top:532px">Welcome to Clinova</h2>
  <div class="abs copy" style="left:200px;top:566px;width:428px">
    <p>Lorem Ipsum is simply dummy text of the printing and typesetting industry. Lorem Ipsum has been the industry's standard dummy text ever since the 1500s, when an unknown printer took a galley of type and scrambled it to make a type specimen book.</p>
    <p style="margin-top:14px">It has survived not only five centuries, but also the leap into electronic typesetting, remaining essentially unchanged. It was popularised in the 1960s with the release of Typeset sheets containing Lorem Ipsum passages, and more recently with desktop publishing software like PageComposer including versions of Lorem Ipsum.</p>
  </div>
  <div class="abs readmore">read more</div>

  <h2 class="abs section-title" style="left:656px;top:532px">How Clinova works?</h2>
  <div class="abs video"><svg width="343" height="128"><path d="M160 50v28l24-14z" fill="#e6eeef"/></svg></div>

  <div class="abs divider"></div>

  <h3 class="abs col-title" style="left:200px">Testimonials</h3>
  <h3 class="abs col-title" style="left:521px">Like Us</h3>
  <h3 class="abs col-title" style="left:774px">Follow Us</h3>

  <div class="abs testi">
    <p>Lorem Ipsum is simply dummy text of the printing and typesetting industry. Lorem Ipsum has been the industry's standard dummy text ever since the 1500s, when an unknown printer took a galley of type and scrambled it to make a type specimen book.</p>
    <p>It has survived not only five centuries, but also the leap into electronic typesetting, remaining essentially unchanged. It was popularised in the 1960s with the release of Typeset sheets containing Lorem Ipsum passages, and more recently with desktop publishing software like PageComposer including versions.</p>
  </div>
  <svg class="abs" style="left:404px;top:951px" width="30" height="22"><path d="M1 0L28 20V0" fill="#fff" stroke="#c9e0e4"/><path d="M0 0H28" stroke="#fff" stroke-width="2"/></svg>
  <div class="abs author"><b>Alex Reid</b>Doctor<br>Northfield University</div>

  <div class="abs likebox">
    <div class="abs" style="left:10px;top:10px;width:30px;height:30px;background:#4f6ea8"></div>
    <div class="abs" style="left:48px;top:9px;font-size:12px;font-weight:700;color:#3b5998">Dev Community</div>
    <div class="abs" style="left:48px;top:26px;border:1px solid #c5cbd8;background:#eef1f7;color:#3b5998;font-size:8px;padding:2px 5px">Like</div>
    <div class="abs" style="left:4px;top:51px;width:215px;height:157px;border:1px solid #ddd;border-left:none"></div>
    <div class="abs" style="left:207px;top:51px;width:11px;height:157px;background:#f1f1f1;border-left:1px solid #ddd"></div>
    <div class="abs" style="left:208px;top:68px;width:9px;height:20px;background:#e1e1e1;border:1px solid #bbb"></div>
    <div class="abs" style="left:8px;top:213px;width:10px;height:10px;background:#3b5998"></div>
    <div class="abs" style="left:23px;top:213px;font-size:7.5px;color:#555">Social plugin</div>
  </div>

  <div class="abs followbox">
    <div class="tweet" style="top:0"><span class="dot"></span><p>Sed mollis eros ut erat condimentum of form congue risus vehicula.<span class="url">http://www.filler-text.example/feed</span><span class="ago">20 mins ago</span></p></div>
    <div class="tweet" style="top:64px"><span class="dot"></span><p>Sed mollis eros ut erat condimentum of form congue risus vehicula.<span class="url">http://www.filler-text.example/feed</span><span class="ago">20 mins ago</span></p></div>
    <div class="tweet" style="top:128px"><span class="dot"></span><p>Sed mollis eros ut erat condimentum of form congue risus vehicula.<span class="url">http://www.filler-text.example/feed</span><span class="ago">20 mins ago</span></p></div>
    <div class="tweet" style="top:192px;border:none"><span class="dot"></span><p>Sed mollis eros ut erat condimentum of form congue risus vehicula.</p></div>
  </div>
</main>

<footer class="abs footer">
  <h3 style="left:200px">Sitemap</h3>
  <ul style="left:200px"><li>Home</li><li>Take the Tour</li><li>What Your Peers Say</li><li>Subscription Plans</li><li>Free Signup</li><li>Contact Us</li><li>Lorem Ipsum</li></ul>
  <ul style="left:326px"><li>Established</li><li>Take the Tour</li><li>What Your Peers Say</li><li>Subscription Plans</li><li>Free Signup</li><li>Contact Us</li><li>Sitemap</li></ul>
  <h3 style="left:467px">Contact Us</h3>
  <div class="contact">Clinova Limited<br>Street Name<br>Lorem Ipsum is simply<br>Country Name<br><span class="strong" style="display:block;margin-top:4px">Phone: 001 555 0142</span><span class="strong">Email: hello@clinova-learn.com</span></div>
  <h3 style="left:619px">Newsletter</h3>
  <div class="news">Join our Newsletter today Sed ut perspiciatis unde omnis iste natus error sit voluptatem accusanti doloremque laudantium, totam rem aperiam, eaque ipsa quae.</div>
  <div class="email">Email</div>
  <div class="join">Join</div>
  <div class="copyright"><svg width="11" height="11"><circle cx="5.5" cy="5.5" r="4.5" fill="none" stroke="#fff" stroke-width="1.3"/><path d="M7.3 4.2a2 2 0 1 0 0 2.6" fill="none" stroke="#fff" stroke-width="1.1"/></svg><br>Copyright 2012 Clinova Limited</div>
</footer>

</body>
</html>
```